Two Versions of a Business Card for a Lawyer

Summary: I need a logo and a business card. The business card is two-sided and comes in two versions. One version is conservative, the other is slightly different with one or more pink embellishments in the logo or somewhere else in the business card.
I'm about to start off as a sole practitioner in criminal and immigration law. I'll largely be working with marginalised communities and in areas of social justice. One of my main focuses will be gendered violence, I'm hoping to specialise my practice towards representing victims of domestic and sexual violence and sex workers. I want a business card which would attract this clientele and make them feel safe to speak with me. I'd also like it to communicate a sense of hope.
However, the business card still has to be very conservative as the legal profession is very stuffy. So I was thinking of having two versions of the same card, one would be very straight forward while the other would have a **pink embellishment** or perhaps several. For example, if the scales of justice were used in the design, maybe the second version would have a pink flower about to bloom on the scale somewhere. Or maybe it's my logo that is different and pink.
While both designs have to be pretty conservative, I still want it to give off a sense that I'm alternative and think outside the box. With lawyers, I think a little bit of deviation goes a long way (less is more).
As far as colour goes (other than the pink embellishment), I was thinking something monochromatic, probably black and white but I am open to considering more colours. I personally love colour, and would love to use more colour, but am hesitant because of the nature of the profession. If you can find a way to use more colour while keeping it conservative and letting the pink pop, I'd be pretty pleased.
In general, I would prefer a clean simplistic design and logo. It should be immediately obvious that I'm a lawyer just by glancing at the card. I'm open to symbols of law, like the scales of justice or lady justice or something else. However, I don't want it to be the same as everyone else's.
Eventually, the design/style should be easy to recreate in the form of a website.
As far as the logo goes, it would probably use a circle as my last name starts with the letter "O". It can be very simple, with just my name and "Barrister & Solicitor". I don't currently have a logo, but the winning designer will be invited to provide a separate file for just the logo for an additional fee (I think it was CA$99). (Please ignore the uploaded logo file, it just wouldn't let me continue without uploading something).
As for the information that should go into the card, I'm still finalizing my address and phone number. So please use a placeholder for now.
Target Market(s)
Women, victims of sexual or domestic violence, refugees, people in need of legal services
Industry/Entity Type
Lawyer
Contact Information for Business Card
Marla Vent
Barrister & Solicitor
LL.B., B.C.L., B.F.A.
Criminal & Immigration Law
Street address
Toronto, ON
Postal Code
Phone number
Fax number
Email
Logo Text
Marla Vent, Barrister & Solicitor
Requirements
Must have
- Two versions
- One with pink
- Simplistic
Nice to have
- Maybe more colour
Should not have
- Not too conservative
- Not too predictable

```html
<!DOCTYPE html>
<html lang="en">
<head>
<meta charset="utf-8">
<title>Marla Vent — Business Card</title>
<link rel="stylesheet" href="https://fonts.googleapis.com/css2?family=Cinzel:wght@400;500&family=Jost:wght@400&family=Pinyon+Script&display=swap">
<style>
  :root {
    --page-bg: #f1f1f1;
    --wash-deep: #a86aa8;
    --wash-mid: #bf8cc0;
    --wash-light: #d9bedb;
    --wash-blue: #b7b2d4;
    --wash-pale: #e6d3e6;
    --ink-plum: #6a2a6e;
    --ink-plum-soft: #7e4a82;
    --white: #ffffff;
  }
  html, body {
    margin: 0;
    width: 1200px;
    height: 1000px;
    overflow: hidden;
    background: var(--page-bg);
  }
  .stage { position: relative; width: 1200px; height: 1000px; }
  .card {
    position: absolute;
    top: 342px;
    width: 550px;
    height: 314px;
    overflow: hidden;
  }
  .card-front { left: 42px; }
  .card-back { left: 614px; }
  .wash { position: absolute; inset: 0; }
  .card-front .wash {
    background:
      radial-gradient(ellipse 220px 120px at 80% 20%, var(--wash-pale) 0%, transparent 70%),
      radial-gradient(ellipse 200px 140px at 20% 85%, var(--wash-blue) 0%, transparent 70%),
      radial-gradient(ellipse 260px 160px at 45% 45%, var(--wash-deep) 0%, transparent 75%),
      linear-gradient(135deg, var(--wash-mid), var(--wash-light));
  }
  .card-back .wash {
    background:
      radial-gradient(ellipse 220px 120px at 40% 30%, var(--wash-blue) 0%, transparent 70%),
      radial-gradient(ellipse 240px 140px at 85% 75%, var(--wash-mid) 0%, transparent 70%),
      radial-gradient(ellipse 200px 120px at 10% 70%, var(--wash-light) 0%, transparent 70%),
      linear-gradient(135deg, var(--wash-pale), var(--wash-light));
  }
  .name-frame {
    position: absolute;
    left: 106px; top: 113px;
    width: 334px; height: 97px;
    border: 1.5px solid var(--white);
    box-sizing: border-box;
  }
  .ornament {
    position: absolute;
    border-radius: 40%;
    background: rgba(255,255,255,0.3);
  }
  .ornament-top { left: 384px; top: 92px; width: 94px; height: 70px; }
  .ornament-bottom { left: 72px; top: 160px; width: 98px; height: 70px; }
  .front-name {
    position: absolute;
    left: 106px; top: 108px;
    width: 334px; height: 97px;
    display: flex; align-items: center; justify-content: center;
    font-family: "Pinyon Script", cursive;
    font-weight: 400;
    font-size: 40px;
    color: var(--white);
  }
  .practice {
    position: absolute; left: 26px; top: 25px; margin: 0;
    font-family: "Cinzel", serif; font-weight: 400;
    font-size: 20.5px; color: var(--ink-plum); letter-spacing: 0.3px;
  }
  .lawyer-name {
    position: absolute; left: 28px; top: 148px; margin: 0;
    font-family: "Cinzel", serif; font-weight: 400;
    font-size: 26px; color: var(--ink-plum); letter-spacing: 0.5px;
  }
  .title {
    position: absolute; left: 28px; top: 186px; margin: 0;
    font-family: "Cinzel", serif; font-size: 13.5px;
    color: var(--ink-plum-soft); line-height: 15px;
  }
  .rule {
    position: absolute; left: 26px; top: 229px;
    width: 490px; height: 1px; background: var(--ink-plum);
  }
  .contact {
    position: absolute; left: 28px; top: 240px; margin: 0;
    font-family: "Jost", sans-serif; font-size: 12px;
    color: var(--ink-plum); white-space: nowrap; letter-spacing: 0.2px;
  }
  .contact .sep { margin: 0 8px; }
  .address {
    position: absolute; left: 29px; top: 264px; margin: 0;
    font-family: "Jost", sans-serif; font-size: 11.8px;
    color: var(--ink-plum); letter-spacing: 1px;
  }
</style>
</head>
<body>
<main class="stage">
  <section class="card card-front">
    <div class="wash" role="img" aria-label="Soft violet watercolour wash background"></div>
    <div class="name-frame"></div>
    <div class="ornament ornament-top" role="img" aria-label="White floral vine ornament"></div>
    <div class="ornament ornament-bottom" role="img" aria-label="White floral vine ornament"></div>
    <div class="front-name">Marla Vent</div>
  </section>

  <section class="card card-back">
    <div class="wash" role="img" aria-label="Pale lilac watercolour wash background"></div>
    <h2 class="practice">CRIMINAL &amp; IMMIGRATION LAW</h2>
    <h1 class="lawyer-name">MARLA VENT</h1>
    <p class="title">Barrister &amp; Solicitor<br>LL.B., B.C.L., B.F.A.</p>
    <div class="rule"></div>
    <p class="contact">Tel: 000.555.1204<span class="sep">|</span>P: 000.555.3916<span class="sep">|</span>F: 000.555.7420<span class="sep">|</span>E: marlavent@mailbox.com</p>
    <p class="address">Your Street Address Here, Toronto, 1234</p>
  </section>
</main>
</body>
</html>
```